Business Card Design

New business card design

Target Market(s)

Residential & Commercial Property Managers

Industry/Entity Type

Plumbing Services

Contact Information for Business Card

Name - Rowan Keddle, title - Director, Phone Number - 0431 286 517, email - rowan@tbk-plumbing.com.au, Company ABN - 73 215 904 386,

Font styles to use
Sans Serif

Colors
0054AA
0677BA
7BADD7
CADEEF
E8F1F8

```html
<!DOCTYPE html>
<html lang="en">
<head>
<meta charset="utf-8">
<title>TBK Plumbing Services – Business Card</title>
<link href="https://fonts.googleapis.com/css2?family=Montserrat:wght@300;400;700&display=swap" rel="stylesheet">
<style>
  :root {
    --backdrop: #d1d5d5;
    --card-stock: #f1f1ef;
    --ink: #1f2326;
    --ink-soft: #6d7073;
    --brand-blue: #1c9bd7;
    --brand-deep: #0677ba;
  }
  html, body {
    margin: 0;
    width: 1200px;
    height: 881px;
    overflow: hidden;
    background: var(--backdrop);
    font-family: "Montserrat", Arial, sans-serif;
  }
  .canvas {
    position: relative;
    width: 1200px;
    height: 881px;
    display: flex;
    align-items: center;
    justify-content: center;
    gap: 44px;
  }
  .card {
    position: relative;
    width: 520px;
    height: 318px;
    background: var(--card-stock);
    border-bottom: 4px solid var(--brand-blue);
    box-shadow: 0 18px 40px rgba(60, 70, 72, 0.25);
    overflow: hidden;
    box-sizing: content-box;
  }
  .wordmark {
    color: var(--ink);
    font-weight: 300;
    letter-spacing: 0.03em;
    white-space: nowrap;
    display: flex;
    align-items: center;
  }
  .wordmark-dot {
    width: 14px;
    height: 14px;
    border-radius: 50%;
    background: var(--brand-blue);
    margin-right: 12px;
    flex: none;
  }
  .front .wordmark {
    position: absolute;
    left: 96px;
    top: 44px;
    font-size: 26px;
    line-height: 32px;
  }
  .name-block {
    position: absolute;
    left: 40px;
    top: 128px;
  }
  .name-bar {
    position: absolute;
    left: 0;
    top: 2px;
    width: 8px;
    height: 30px;
    background: var(--brand-blue);
  }
  .person-name {
    margin: 0 0 0 20px;
    font-size: 24px;
    font-weight: 700;
    color: var(--brand-blue);
    line-height: 34px;
  }
  .person-title {
    margin: 2px 0 0 20px;
    font-size: 15px;
    font-weight: 400;
    line-height: 20px;
    color: var(--ink);
  }
  .divider {
    position: absolute;
    left: 0;
    top: 0;
  }
  .contact-list {
    position: absolute;
    left: 44px;
    top: 212px;
    margin: 0;
    padding: 0;
    list-style: none;
    font-size: 14px;
    color: var(--ink);
  }
  .contact-list li {
    display: flex;
    align-items: center;
    gap: 8px;
    height: 24px;
  }
  .abn {
    position: absolute;
    right: 40px;
    top: 270px;
    margin: 0;
    font-size: 14px;
    line-height: 18px;
    color: var(--ink);
  }
  .back .wordmark {
    position: absolute;
    left: 24px;
    right: 24px;
    top: 136px;
    justify-content: center;
    font-size: 32px;
    line-height: 40px;
  }
  .back .wordmark-dot {
    width: 16px;
    height: 16px;
    margin-right: 14px;
  }
</style>
</head>
<body>
<main class="canvas">
  <section class="card front" aria-label="Business card, contact side">
    <div class="wordmark"><span class="wordmark-dot"></span>TBK Plumbing Services</div>

    <div class="name-block">
      <span class="name-bar"></span>
      <p class="person-name">Rowan Keddle</p>
      <p class="person-title">Director</p>
    </div>

    <svg class="divider" width="520" height="318" viewBox="0 0 520 318" aria-hidden="true">
      <path d="M40 203 H300 C318 203 322 258 342 258 H482" fill="none" stroke="var(--brand-blue)" stroke-width="1.5"/>
    </svg>

    <ul class="contact-list">
      <li>
        <svg width="12" height="12" viewBox="0 0 24 24" aria-hidden="true"><path d="M6.6 10.8a15 15 0 0 0 6.6 6.6l2.2-2.2c.3-.3.7-.4 1-.2 1.1.4 2.3.6 3.6.6.6 0 1 .4 1 1V20c0 .6-.4 1-1 1A17 17 0 0 1 3 4c0-.6.4-1 1-1h3.5c.6 0 1 .4 1 1 0 1.3.2 2.5.6 3.6.1.3 0 .7-.2 1z" fill="var(--brand-blue)"/></svg>
        0431 286 517
      </li>
      <li>
        <svg width="12" height="12" viewBox="0 0 24 24" aria-hidden="true"><rect x="2" y="5" width="20" height="14" rx="2" fill="var(--brand-blue)"/><path d="M3 6l9 7 9-7" fill="none" stroke="#fff" stroke-width="1.8"/></svg>
        rowan@tbk-plumbing.com.au
      </li>
    </ul>

    <p class="abn">Company ABN - 73 215 904 386</p>
  </section>

  <section class="card back" aria-label="Business card, brand side">
    <div class="wordmark"><span class="wordmark-dot"></span>TBK Plumbing Services</div>
  </section>
</main>
</body>
</html>
```